VORNAK SYSTEMS BUSINESS CARD DESIGN

WE WANT COMPLETE NEW DESIGN OF OUR BUSINESS CARD. WE ARE AN INTEGRATION COMPANY, WHERE WE INTEGRATE IOT/SMART SYSTEMS TO HOMES AND CORPORATE CUSTOMERS. WE SUPPLY AND INSTALL AUTOMATION PRODUCTS. THE FINAL DESIGN SHOULD COMMUNICATE TECHNOLOGY. THE CARD DESIGN SHOULD BE VERY IMPACT FULL. LOGO NEEDS TO BE THERE. IT WOULD NICE IF THE DESIGN WAS CLEAN. COLORS IS UP TO DESIGNER TO PLAY WITH, OR CAN STICK TO CORPORATE COLORS (FOLLOW LOGO). I HAVE ADDED FEW REFERENCE PHOTOS TO DRAW INSPIRATION MAYBE. I HAVE ADDED A HEX DESIGN, ITS NOT NECESSARY TO USE THIS DESIGN, ITS UPTO DESIGNER, JUST ADDED IF NEEDED TO PLAY WITH DESIGN.

Target Market(s)

Private end users and corporate clients

Industry/Entity Type

technology, home automation, home theaters, building management systems, IOT

Contact Information for Business Card

It should include Employee name, personal number, office number, email address, both in English and arabic. DETAILS TO INCLUDE :RAJESH PALLIVAL, MOBILE 0097150738265,OFFCIE 009714368547, RAJESH@VORNAKSYS.EXAMPLE

Requirements
Must have
• Should feel like a technology company from design. Details both and in English and arabic (or at least have provision for arabic in design).
Nice to have
• I would like logo on one side, and details on the other side. Logo design side should communicate technology with logo. Other side can be clean just with information or also have some design aspects following from logo side. it would be interesting to see submissions with square design as well (that looks like an app Icon). colors could be of logo, red black grey and white. I have added some designs to draw inspiration from

```html
<!DOCTYPE html>
<html lang="en">
<head>
<meta charset="utf-8">
<title>Vornak Systems Business Card</title>
<link rel="stylesheet" href="https://fonts.googleapis.com/css2?family=Roboto:wght@400;500;700&family=Michroma&display=swap">
<style>
:root{
  --stage:#2b2b2b;
  --card-black:#000000;
  --white:#f2f2f2;
  --grey:#c9c9c9;
  --red:#e3202b;
  --facet-a:#1fc7b4;
  --facet-b:#e8b21a;
  --facet-c:#d8242f;
  --facet-d:#3a3fa8;
  --facet-e:#6ad3e6;
}
*{margin:0;padding:0;box-sizing:border-box}
html,body{width:1200px;height:1138px;overflow:hidden;background:var(--stage)}
.stage{position:relative;width:1200px;height:1138px}
.card{position:absolute;width:622px;height:376px}
.card--front{left:272px;top:184px}
.card--back{left:274px;top:606px}
.card__frame{
  position:absolute;inset:0;
  background:
    linear-gradient(135deg,var(--facet-a) 0%,var(--facet-b) 22%,var(--facet-c) 40%,var(--facet-d) 58%,var(--facet-e) 76%,var(--facet-b) 100%);
}
.card__panel{
  position:absolute;left:13px;right:13px;top:11px;bottom:11px;
  background:var(--card-black);
}
.brand{
  display:flex;align-items:center;gap:12px;
  font-family:"Roboto",sans-serif;font-weight:700;color:var(--white);
  letter-spacing:.06em;
}
.brand__dot{width:22px;height:22px;border-radius:50%;background:var(--red);flex:none}
.card--front .brand{
  position:absolute;left:0;right:0;top:50%;transform:translateY(-50%);
  justify-content:center;font-size:34px;
}
.back__header{position:absolute;left:26px;top:46px}
.back__header .brand{font-size:32px}
.back__header .brand__dot{width:20px;height:20px}
.back__sub{
  font-family:"Roboto",sans-serif;font-weight:500;color:var(--grey);
  font-size:15px;letter-spacing:.04em;margin:4px 0 0 90px;
}
.back__tagline{
  font-family:"Michroma",sans-serif;color:var(--white);
  font-size:10.5px;letter-spacing:.14em;margin-top:8px;
}
.person{
  position:absolute;left:26px;top:194px;
  font-family:"Roboto",sans-serif;font-weight:500;color:var(--red);font-size:24px;
}
.contacts{position:absolute;left:32px;top:240px;list-style:none}
.contacts li{
  display:flex;align-items:center;gap:12px;height:24px;
  font-family:"Roboto",sans-serif;font-size:16px;color:var(--white);
}
.contacts svg{width:12px;height:12px;flex:none}
.back__mark{
  position:absolute;left:320px;top:120px;width:270px;
  font-family:"Roboto",sans-serif;font-weight:700;color:var(--white);
  font-size:46px;line-height:1.05;letter-spacing:.04em;text-align:center;
}
</style>
</head>
<body>
<main class="stage">
  <section class="card card--front">
    <div class="card__frame" role="img" aria-label="Multicoloured faceted polygon border"></div>
    <div class="card__panel">
      <div class="brand"><span class="brand__dot"></span>VORNAK SYSTEMS</div>
    </div>
  </section>

  <section class="card card--back">
    <div class="card__frame" role="img" aria-label="Multicoloured faceted polygon border"></div>
    <div class="card__panel">
      <header class="back__header">
        <div class="brand"><span class="brand__dot"></span>VORNAK SYSTEMS</div>
        <p class="back__sub">SYSTEMS L.L.C</p>
        <p class="back__tagline">A VORNAK GROUP DIVISION.</p>
      </header>
      <h1 class="person">Rajesh Pallival</h1>
      <ul class="contacts">
        <li><svg viewBox="0 0 12 12"><rect x="3" y="0.8" width="6" height="10.4" rx="1.2" fill="none" stroke="var(--red)" stroke-width="1.3"/><circle cx="6" cy="9.3" r=".7" fill="var(--red)"/></svg>0097150738265</li>
        <li><svg viewBox="0 0 12 12"><circle cx="6" cy="6" r="5.2" fill="none" stroke="var(--red)" stroke-width="1.2"/><path d="M4 3.3l1 1.2-.6.8c.4.8 1 1.4 1.8 1.8l.8-.6 1.2 1-.6 1C5.4 8.3 3.7 6.6 3.3 4z" fill="var(--red)"/></svg>009714368547</li>
        <li><svg viewBox="0 0 12 12"><rect x=".8" y="2.2" width="10.4" height="7.6" fill="none" stroke="var(--red)" stroke-width="1.2"/><path d="M1 2.5l5 4 5-4" fill="none" stroke="var(--red)" stroke-width="1.2"/></svg>rajesh@vornaksys.example</li>
        <li><svg viewBox="0 0 12 12"><circle cx="6" cy="6" r="5.2" fill="none" stroke="var(--red)" stroke-width="1.2"/><ellipse cx="6" cy="6" rx="2.2" ry="5.2" fill="none" stroke="var(--red)" stroke-width="1"/><path d="M.8 6h10.4" stroke="var(--red)" stroke-width="1"/></svg>www.vornaksys.example</li>
      </ul>
      <div class="back__mark">VORNAK<br>SYSTEMS</div>
    </div>
  </section>
</main>
</body>
</html>
```